New Business card design to reflect rebrand

I would like a business card design with a good base colour for our new logo and also a placeholder for a profile pic of the card holder. the design needs to be editable to the point that we can easily change the picture of the person and use that design for printmerlo etc. we are looking at a metalic finish business card so will need a good base colour to bring out the finish.

Target Market(s)

prospective customers

Industry/Entity Type

Business

Contact Information for Business Card

I would like one editable design that we can change the name of the card holder and profile picture. The design need to be in a format that be send to printmerlo etc.

Our address is Fenwick Lodge, Copse Lane, Elmsted Cross, GU14 3TP Tel no. 01483 556172

Requirements
Must have
• place holder for a profile pic for the card holder. in AI or preferably PSD format

```html
<!DOCTYPE html>
<html lang="en">
<head>
<meta charset="utf-8">
<title>Larchfield Workplace Services – Business Card</title>
<link rel="stylesheet" href="https://fonts.googleapis.com/css2?family=Open+Sans:wght@400;600&family=Exo+2:wght@700&display=swap">
<style>
  :root {
    --backdrop: #3a3330;
    --card-white: #f7f7f6;
    --card-black: #1c1d1f;
    --brand-slate: #4b6180;
    --brand-orange: #ee6a1c;
    --ink: #2b2b2b;
    --photo-light: #e9ecef;
    --photo-dark: #3a4150;
  }
  * { box-sizing: border-box; margin: 0; padding: 0; }
  html, body { width: 1200px; height: 844px; overflow: hidden; }
  body {
    background: var(--backdrop);
    font-family: "Open Sans", Arial, sans-serif;
    position: relative;
  }
  .card {
    position: absolute;
    top: 254px;
    width: 520px;
    height: 336px;
    border-radius: 4px;
    overflow: hidden;
    box-shadow: 0 10px 28px rgba(0,0,0,.45);
  }
  .card--front { left: 60px; background: var(--card-white); }
  .card--back  { left: 620px; background: var(--card-black); }

  .brand {
    position: absolute;
    display: flex;
    align-items: center;
    gap: 10px;
    font-family: "Exo 2", "Open Sans", sans-serif;
    font-weight: 700;
    color: var(--brand-slate);
    line-height: 1.05;
    text-transform: uppercase;
  }
  .brand__mark { width: 14px; height: 14px; background: var(--brand-orange); flex: none; }
  .brand__name { font-size: 24px; letter-spacing: 1px; }
  .brand__name small { display: block; font-size: 13px; letter-spacing: 2.5px; }
  .card--front .brand { top: 38px; right: 30px; }
  .card--back .brand { top: 50%; left: 50%; transform: translate(-50%, -50%); }
  .card--back .brand__name { font-size: 32px; }
  .card--back .brand__name small { font-size: 17px; }

  .contact {
    position: absolute;
    left: 300px;
    top: 130px;
    font-size: 12.5px;
    color: var(--ink);
    line-height: 1.7;
  }
  .contact__row { display: flex; align-items: center; gap: 7px; }
  .contact__row svg { width: 11px; height: 11px; fill: var(--brand-slate); }
  .contact__address { margin-top: 20px; line-height: 1.55; }

  .profile-photo {
    position: absolute;
    left: 0;
    bottom: 0;
    width: 290px;
    height: 236px;
    background: linear-gradient(160deg, var(--photo-light) 0%, #cbb49c 40%, var(--photo-dark) 100%);
  }
  .holder-name {
    position: absolute;
    left: 30px;
    bottom: 22px;
    font-family: "Exo 2", "Open Sans", sans-serif;
    font-weight: 700;
    font-size: 26px;
    letter-spacing: .5px;
    color: var(--brand-slate);
    background: var(--card-white);
    padding: 2px 10px;
    border-radius: 4px;
  }
  .holder-name__last { color: var(--brand-orange); }
</style>
</head>
<body>
  <section class="card card--front" aria-label="Business card front">
    <div class="profile-photo" role="img" aria-label="Profile photo of the card holder"></div>
    <div class="brand">
      <span class="brand__mark"></span>
      <span class="brand__name">Larchfield<small>Workplace Services</small></span>
    </div>
    <div class="contact">
      <div class="contact__row">
        <svg viewBox="0 0 24 24"><path d="M6.6 10.8a15 15 0 0 0 6.6 6.6l2.2-2.2a1 1 0 0 1 1-.25 11.4 11.4 0 0 0 3.6.57 1 1 0 0 1 1 1V20a1 1 0 0 1-1 1A17 17 0 0 1 3 4a1 1 0 0 1 1-1h3.5a1 1 0 0 1 1 1c0 1.250.2 2.45.57 3.57a1 1 0 0 1-.25 1z"/></svg>
        <span>01483 556172</span>
      </div>
      <div class="contact__row">
        <svg viewBox="0 0 24 24"><path d="M2 5h20v14H2z M2 5l10 8 10-8" /></svg>
        <span>info@larchfieldws.com</span>
      </div>
      <p class="contact__address">Fenwick Lodge, Copse Lane,<br>Elmsted Cross, GU14 3TP</p>
    </div>
    <p class="holder-name">TOM <span class="holder-name__last">HARLOW</span></p>
  </section>

  <section class="card card--back" aria-label="Business card back">
    <div class="brand">
      <span class="brand__mark"></span>
      <span class="brand__name">Larchfield<small>Workplace Services</small></span>
    </div>
  </section>
</body>
</html>
```